TRESSES BY JOLAVIE

We need a web design for a company base in Chicago called Tresses by Jolavie. We sale 100% human hair in Brazilian body wave deep wave straight or natural curl, Peruvian body wave straight or deep wave. Malaysian loose straight or body wave, in the chicago land.
We also ship hair to any city or country. We like to see design that use the colors pinks & grays, or would just like to see some design creative with colors thats inviting.

Also I'm using the quillmoss template, Home- banner contact us, about us, Features- product side/left sidebar, Shop- wish list /shopping cart/ tracking your order / checkout/ order received.
Porfolio-filterable 4column portfolio
Blog. Buy now

Industry/Entity Type

Hair

Number of Pages Required

4 page

Colors
aaaaaa
606060
dddddd
eea4c8
d3a5cc
b868aa
a6459a
ffc213
1b1b1b

Requirements
Must have
• I NEED THE DESIGNER TO DO THE 4 PAGE LIKE THIS.
• 1.HOME-PAGE BANNER CONTACT US SOME PRODUCT WITH SIDING IMAGES OF THE TOP PROUDCT
• 2.PRODUCT WITH SHOPPING CART- I WANT SIDING BARS FOR PRODUCT & SHOPPING CART WITH TRACKING YOUR ORDERS CHECK OUT & ORDER RECEIVED.
• 3.PORFOLIO PHOTO-I WANT A FEATURES FOR CUSTOMERS TO UPLOAN THERE PICTURE & BLOG ON THE PAGE
• 4.ABOUT US- TALK ABOUT ARE COMPAMY.
Nice to have
• hello designer
• I was working with a web developer for my site be for i came to craftnookly & they build a site for me that i liked, You all can view it at www.Tressesbyjolavie.info
• long story short never could get them to finish the project after they got paid!!
• I know, why paid before its finish bad decision. So know I'm here starting over with you all.
• here is a list of my competition site
• www.lockswellhub.com
• www.vanoraloft.com
• www.pellinoshop.com
• So just to give some insight, I'm looking for something like the one i had builded.

```html
<!DOCTYPE html>
<html lang="en">
<head>
<meta charset="utf-8">
<title>Tresses by Jolavie</title>
<link href="https://fonts.googleapis.com/css2?family=Arimo:wght@400;700&family=Didact+Gothic&family=Open+Sans:wght@600;700&display=swap" rel="stylesheet">
<style>
:root{
  --pink:#e5087f;
  --ink:#1b1b1b;
  --bar:#2b2b2b;
  --grey:#606060;
  --mist:#dcddd8;
  --line:#dddddd;
  --footer:#bdbdbd;
  --white:#ffffff;
  --hair-dark:#2a2327;
  --skin:#e2b7a3;
}
*{margin:0;padding:0;box-sizing:border-box}
html,body{width:810px;height:1200px;overflow:hidden;background:var(--white)}
body{position:relative;font-family:"Arimo",Arial,sans-serif;color:var(--ink)}
.abs{position:absolute}
/* header */
.topbar{left:0;top:0;width:810px;height:59px;background:var(--bar)}
.brand-plate{left:0;top:0}
.brand{left:86px;top:12px;font-family:"Didact Gothic",sans-serif;font-size:28px;color:var(--pink);white-space:nowrap}
.shop-links{right:68px;top:15px;color:var(--white);font-size:10px;text-align:right;line-height:20px}
.shop-links .sep{margin:0 9px}
.shop-links svg{vertical-align:-3px;margin:0 4px 0 6px}
.shop-links small{font-size:7px}
/* nav */
.nav{top:59px;left:0;width:810px;height:35px;border-bottom:1px solid #eee}
.nav a{position:absolute;top:10px;font-family:"Didact Gothic",sans-serif;font-size:12px;color:var(--ink);text-decoration:none;letter-spacing:.5px}
.nav .active:after{content:"";position:absolute;left:-7px;right:-7px;top:22px;height:4px;background:var(--pink)}
.search{left:532px;top:7px;width:210px;height:21px;border:1px solid var(--line);font-size:9px;color:#555;padding:5px 7px}
.search svg{position:absolute;right:3px;top:2px}
.search:before{content:"";position:absolute;right:26px;top:3px;height:14px;border-left:1px solid var(--line)}
/* hero */
.hero{top:94px;left:0;width:810px;height:380px;background:linear-gradient(90deg,#f3f2f0 0%,#e7e7e3 55%,var(--mist) 100%)}
.hero-photo{left:0;top:0;width:400px;height:380px;
  background:
    linear-gradient(90deg,rgba(243,242,240,0) 78%,#f1f0ee 100%),
    linear-gradient(90deg,var(--hair-dark) 0%,#3a3034 30%,var(--skin) 52%,#d49c86 70%,#efe6e1 88%);}
.hero h1{left:392px;top:132px;font-family:"Didact Gothic",sans-serif;font-weight:400;font-size:31px;color:var(--ink);white-space:nowrap;letter-spacing:.2px}
.hero h2{left:392px;top:170px;font-family:"Didact Gothic",sans-serif;font-weight:400;font-size:40px;color:var(--pink);white-space:nowrap;-webkit-text-stroke:.8px var(--pink)}
.hero p{left:394px;top:225px;width:330px;font-size:9.6px;line-height:15px;color:#444}
.btn{background:var(--pink);color:var(--white);text-align:center}
.hero .btn{left:620px;top:274px;width:122px;height:36px;font-size:17px;line-height:36px}
/* products */
.section-title{left:66px;top:508px;font-family:"Open Sans",sans-serif;font-weight:600;font-size:16.5px}
.arrow{top:508px;width:19px;height:19px;border:1.5px solid var(--ink)}
.card{top:546px;width:152px}
.card .photo{position:relative;width:152px;height:188px}
.card .name{margin-top:9px;text-align:center;font-size:9.5px;font-weight:700;color:#444}
.card .price{margin-top:4px;text-align:center;font-size:10px;font-weight:700;color:var(--pink)}
.card .price s{color:#777;font-weight:400;margin-left:3px}
.photo-a{background:linear-gradient(90deg,#f4f1ef 0%,#f4f1ef 18%,#7b4f3a 30%,#e7c2ae 45%,#e7c2ae 58%,#7b4f3a 72%,#f4f1ef 84%)}
.photo-b{background:linear-gradient(90deg,#f7eff1 0%,#f7eff1 8%,#3b3132 22%,#d8bfb4 42%,#d8bfb4 56%,#3b3132 76%,#f7eff1 94%)}
.photo-c{background:linear-gradient(90deg,#5a3a34 0%,#e6cfa0 20%,#efc4b0 40%,#efc4b0 55%,#e8b986 66%,#e5609a 80%,#d9437f 92%,#5a3a34 100%)}
.photo-d{background:linear-gradient(90deg,#ededed 0%,#ededed 8%,#7b5a3e 22%,#b88e6c 34%,#e4bfa6 46%,#e4bfa6 58%,#b88e6c 70%,#7b5a3e 84%,#ededed 96%)}
.tools{left:0;top:144px;width:152px;height:23px;background:rgba(70,70,70,.8);display:flex;justify-content:center;gap:7px;align-items:center}
.tools span{width:15px;height:15px;border-radius:50%;background:var(--white)}
.cart-bar{left:0;top:167px;width:152px;height:21px;line-height:21px;font-size:11px;font-weight:700}
.sale{right:0;top:0}
/* contact */
.contact{top:826px;left:0;width:810px;height:308px;background:linear-gradient(100deg,#3b3736 0%,#4a4442 35%,#6d6b6b 60%,#8d8c8e 100%)}
.contact h3{left:0;width:784px;text-align:center;top:30px;font-family:"Open Sans",sans-serif;font-weight:700;font-size:32px;color:var(--white);letter-spacing:1px}
.field{left:67px;width:289px;background:#f2f2f2;border:1px solid #ccc;font-size:10.5px;color:#333;padding:8px 13px}
.info-title{left:415px;top:89px;font-size:17.5px;color:var(--white);letter-spacing:1px}
.info{left:415px;color:var(--white);font-size:14px;display:flex;align-items:center;gap:12px}
.social{top:201px;width:16px;height:16px;background:#bbb;border-radius:2px}
.contact .btn{left:416px;top:238px;width:83px;height:31px;line-height:29px;font-size:18px;border:1px solid var(--white);letter-spacing:1px}
/* footer */
.footer{top:1134px;left:0;width:810px;height:66px;background:var(--footer);border-top:2px solid #d6d6d6}
.footer-links{left:71px;top:15px;font-size:9.5px;color:var(--ink)}
.footer-links .sep{margin:0 14px}
.copy{left:69px;top:41px;font-size:9.5px;color:var(--ink)}
.pay{left:620px;top:16px;width:109px;height:34px;border:1px solid #6f8fb8;border-radius:3px;background:#e9edf3}
</style>
</head>
<body>

<header>
  <div class="abs topbar"></div>
  <svg class="abs brand-plate" width="370" height="59"><polygon points="80,0 363,0 331,59 43,59" fill="#fff"/></svg>
  <div class="abs brand">Tresses by Jolavie</div>
  <div class="abs shop-links">
    <div>Shopping Cart<svg width="14" height="13" viewBox="0 0 14 13"><path d="M0 1h2.5l2 7h7l1.5-5H4" fill="none" stroke="#fff" stroke-width="1.4"/><circle cx="5.5" cy="11" r="1.3" fill="#fff"/><circle cx="10.5" cy="11" r="1.3" fill="#fff"/></svg><b>Cart:</b> <small>(empty)</small></div>
    <div>My Account<span class="sep">|</span>Checkout<span class="sep">|</span>Order Received</div>
  </div>
</header>

<nav class="abs nav">
  <a class="active" style="left:74px">Home</a>
  <a style="left:143px">banner</a>
  <a style="left:224px">contact us</a>
  <a style="left:321px">about us</a>
  <div class="abs search">tracking your order
    <svg width="17" height="17" viewBox="0 0 17 17"><circle cx="7" cy="7" r="5.5" fill="none" stroke="#555" stroke-width="1.6"/><line x1="11" y1="11" x2="15.5" y2="15.5" stroke="#555" stroke-width="2"/></svg>
  </div>
</nav>

<section class="abs hero">
  <div class="abs hero-photo" role="img" aria-label="Photo of a woman with long dark curly hair looking over her shoulder"></div>
  <h1 class="abs">Get The Long Hair You’ve</h1>
  <h2 class="abs">Never Had Before!</h2>
  <p class="abs">Lorem ipsum dolor sit amet, consectetur adipiscing elit, sed do eiusmod tempor incididunt ut labore et dolore magna aliqua.</p>
  <div class="abs btn">Shope Now</div>
</section>

<section>
  <div class="abs section-title">Featured Product</div>
  <svg class="abs arrow" style="left:691px" viewBox="0 0 19 19"><path d="M11 5l-4 4.5 4 4.5" fill="none" stroke="#1b1b1b" stroke-width="1.4"/></svg>
  <svg class="abs arrow" style="left:714px" viewBox="0 0 19 19"><path d="M8 5l4 4.5-4 4.5" fill="none" stroke="#1b1b1b" stroke-width="1.4"/></svg>

  <div class="abs card" style="left:67px">
    <div class="photo photo-a" role="img" aria-label="Model with long brown layered hair">
      <svg class="abs sale" width="26" height="26"><polygon points="0,0 26,0 26,26" fill="#e5087f"/><text x="17" y="10" font-size="5.5" fill="#fff" font-family="Arimo" transform="rotate(45 17 10)" text-anchor="middle">SALE</text></svg>
      <div class="abs tools"><span></span><span></span><span></span></div>
      <div class="abs btn cart-bar">ADD TO CART</div>
    </div>
    <div class="name">Lorem Ipsum is</div>
    <div class="price">$1170.46 <s>$1.300</s></div>
  </div>
  <div class="abs card" style="left:242px">
    <div class="photo photo-b" role="img" aria-label="Model with long dark wavy hair"></div>
    <div class="name">Lorem Ipsum is</div>
    <div class="price">$1170.46 <s>$1.300</s></div>
  </div>
  <div class="abs card" style="left:416px">
    <div class="photo photo-c" role="img" aria-label="Model with blonde hair and pink streaks"></div>
    <div class="name">Lorem Ipsum is</div>
    <div class="price">$1170.46 <s>$1.300</s></div>
  </div>
  <div class="abs card" style="left:588px">
    <div class="photo photo-d" role="img" aria-label="Model with long light brown curly hair"></div>
    <div class="name">Lorem Ipsum is</div>
    <div class="price">$1170.46 <s>$1.300</s></div>
  </div>
</section>

<section class="abs contact" role="img" aria-label="Background photo of a stylist blow-drying hair">
  <h3 class="abs">CONTACT</h3>
  <div class="abs field" style="top:84px;height:30px">Full Name</div>
  <div class="abs field" style="top:124px;height:30px">Email</div>
  <div class="abs field" style="top:168px;height:104px">Message</div>
  <div class="abs info-title">CONTACT INFO</div>
  <div class="abs info" style="top:132px"><svg width="19" height="19" viewBox="0 0 19 19"><circle cx="9.5" cy="9.5" r="8.5" fill="none" stroke="#e5087f" stroke-width="1.6"/><path d="M6 5c-1 1-1 3 1 5.5s4.5 3 5.5 2l.8-.9-2-1.6-1 .8c-1-.5-2-1.6-2.5-2.6l.8-1L7.9 5.2z" fill="#e5087f"/></svg>5550148267</div>
  <div class="abs info" style="top:168px"><svg width="19" height="14" viewBox="0 0 19 14"><rect width="19" height="14" fill="#e5087f"/><path d="M0 0l9.5 7L19 0" fill="none" stroke="#fff" stroke-width="1"/></svg>hello@tressesbyjolavie.com</div>
  <div class="abs social" style="left:418px"></div>
  <div class="abs social" style="left:445px"></div>
  <div class="abs btn">SEND</div>
</section>

<footer class="abs footer">
  <div class="abs footer-links">Home<span class="sep">|</span>banner<span class="sep">|</span>contact us<span class="sep">|</span>about us</div>
  <div class="abs copy">© 2014 Copyright Jolavie Studio. All Rights Reserved.</div>
  <div class="abs pay"></div>
</footer>

</body>
</html>
```